Marwick Law Letterhead

We need a new letterhead design for a Law Firm. The address for the law firm is 1475 Calloway Street, Suite 210, Houston, Texas 77041. Phone Number: 832-361-9027; Fax Number: 832-614-7359. The logo is uploaded to the project.

```html
<!DOCTYPE html>
<html lang="en">
<head>
<meta charset="utf-8">
<title>Marwick Law Letterhead</title>
<link rel="stylesheet" href="https://fonts.googleapis.com/css2?family=Montserrat:wght@300;400;500&family=Tinos&display=swap">
<style>
  :root {
    --navy: #1b2a5c;
    --navy-deep: #14204a;
    --red: #d72a26;
    --text: #8c8c8c;
    --ink: #3a3a3a;
    --paper: #ffffff;
    --backdrop: #d9dadc;
  }
  * { margin: 0; padding: 0; box-sizing: border-box; }
  html, body { width: 1200px; height: 1200px; overflow: hidden; background: var(--backdrop); }
  .canvas { position: relative; width: 1200px; height: 1200px; overflow: hidden; }
  .letterhead {
    position: absolute; left: 226px; top: 56px;
    width: 934px; height: 1321px;
    background: var(--paper);
    transform: scale(0.8); transform-origin: 0 0;
    font-family: "Montserrat", sans-serif;
  }
  .header-band { position: absolute; left: 0; top: 42px; width: 604px; height: 77px; }
  .header-band .rule-top { position: absolute; left: 0; top: 0; width: 100%; height: 7px; background: var(--navy); }
  .header-band .rule-red { position: absolute; left: 0; top: 12px; width: 100%; height: 7px; background: var(--red); }
  .header-band .band { position: absolute; left: 0; top: 19px; width: 100%; height: 58px; background: linear-gradient(90deg, var(--navy) 0%, var(--navy-deep) 100%); }
  .contact {
    position: absolute; left: 43px; top: 10px;
    display: flex; align-items: center;
    font-family: "Tinos", serif; font-size: 15px; color: #fff; line-height: 19px;
  }
  .contact .phones { padding-right: 10px; border-right: 1.5px solid #fff; }
  .contact .phones div { display: flex; align-items: center; gap: 7px; }
  .contact .phones svg { width: 13px; height: 13px; fill: #fff; }
  .contact .address { padding-left: 12px; }
  .brand {
    position: absolute; left: 614px; top: 58px;
    display: flex; align-items: center; gap: 14px;
  }
  .brand .mark { width: 34px; height: 34px; background: var(--navy); }
  .brand .name { font-family: "Tinos", serif; font-size: 38px; color: var(--navy); letter-spacing: 0.5px; }
  .recipient { position: absolute; left: 95px; top: 294px; }
  .recipient .to { font-size: 16px; letter-spacing: 3px; color: var(--ink); }
  .recipient .person { margin-top: 7px; font-size: 15.5px; color: var(--red); }
  .recipient .lines { margin-top: 6px; font-size: 13px; line-height: 20.7px; color: var(--text); }
  .date { position: absolute; right: 94px; top: 293px; font-size: 13.5px; color: var(--ink); }
  .body-copy {
    position: absolute; left: 95px; top: 472px; width: 746px;
    font-size: 13.6px; font-weight: 300; letter-spacing: -0.15px;
    line-height: 16.6px; color: var(--text); text-align: justify;
  }
  .body-copy p { margin-bottom: 16.6px; }
  .signature { position: absolute; left: 95px; top: 934px; width: 160px; height: 34px; background: linear-gradient(90deg, #d8d8d8, #ececec); }
  .signer { position: absolute; left: 93px; top: 982px; }
  .signer .name { font-size: 15.5px; color: var(--ink); }
  .signer .role { margin-top: 2px; font-size: 12.5px; color: var(--text); }
</style>
</head>
<body>
<div class="canvas">
  <div class="letterhead">
    <div class="header-band">
      <div class="rule-top"></div>
      <div class="rule-red"></div>
      <div class="band">
        <div class="contact">
          <div class="phones">
            <div><svg viewBox="0 0 24 24"><path d="M6.6 10.8a15.1 15.1 0 0 0 6.6 6.6l2.2-2.2c.3-.3.7-.4 1-.2 1.1.4 2.3.6 3.6.6.6 0 1 .4 1 1V20c0 .6-.4 1-1 1A17 17 0 0 1 3 4c0-.6.4-1 1-1h3.5c.6 0 1 .4 1 1 0 1.3.2 2.5.6 3.6.1.3 0 .7-.2 1z"/></svg>832-361-9027</div>
            <div><svg viewBox="0 0 24 24"><path d="M7 3h10v5H7zM4 9h16a2 2 0 0 1 2 2v7h-4v3H6v-3H2v-7a2 2 0 0 1 2-2zm4 8v2h8v-2z"/></svg>832-614-7359</div>
          </div>
          <div class="address">
            <div>1475 Calloway Street</div>
            <div>Suite 210, Houston, Texas 77041</div>
          </div>
        </div>
      </div>
    </div>
    <div class="brand">
      <div class="mark"></div>
      <div class="name">Marwick Law</div>
    </div>

    <div class="recipient">
      <div class="to">TO</div>
      <div class="person">Daniel Ferrow</div>
      <div class="lines">
        <div>Human Resources</div>
        <div>Brightline Systems Inc.</div>
        <div>1208-B Linden Court, Oakfield</div>
        <div>E89 USA</div>
      </div>
    </div>
    <div class="date">Friday, 01/01/2018</div>

    <div class="body-copy">
      <p>Lorem ipsum dolor sit amet, consectetuer adipiscing elit, sed diam nonmmy nibh euismod tincidunt ut laoreet dolore magna aliquam erat volutpat. Ut wisi enim ad minim veniam, quis nostrud exerci tationmcorper suscipit lobortis nisl ut aliquip ex ea commodo consequat. Duis autem vel eum iriure dolor in hendrerit in vulputate velit esse molestie consequat, vel illum dolore eu feugiat nulla facilisis at vero eros et accumsan et iusto odio dignissim qui blandit praesent luptatum zzril delenit augue duis dolore te feugait nulla facilisi.</p>
      <p>Nam liber tempor cum soluta nobis eleifend option congue nihil imprdiet doming id quod mazim placerat facer possim assum. Typi non habent claritatem insitam;</p>
      <p>Est usus legentis in iis qui facit eorum claritatem.</p>
      <p>Investigationes demonstraverunt lectores legere me lius quod ii legunt saepius. Claritas est etiam processus dynamicus, qui sequitur mutationem consuetudium lectorum. Mirum est notare quam littera gothica, quam nunc putamus parum claram, anteposuerit litterarum formas humanitatis per seacula quarta decima et quinta decima. Eodem modo typi, qui nunc nobis videntur parum clari, fiant sollemnes in futurum.</p>
      <p>consectetuer adipiscing elit, sed diam nonummy nibh euismod tincidunt ut laoreet dolore magna aliquam erat volutpat. Ut wisi enim ad minim veniam, quis nostrud exerci tation ullamcorper suscipit lobortis nisl ut aliquip ex ea commodo consequat. Duis autem vel eum iriure dolor in hendrerit in vulputate velit esse molestie consequat, vel illum dolore eu feugiat nulla facilisis at vero eros et accumsan et iusto odio dignissim qui blandit praesent luptatum zzril delenit augue duis dolore te feugait nulla facilisi.</p>
      <p>Nam liber tempor cum soluta nobis eleifend option congue nihil imperdiet .</p>
    </div>

    <div class="signature" role="img" aria-label="Handwritten signature of Henry Caldwell"></div>
    <div class="signer">
      <div class="name">Henry Caldwell</div>
      <div class="role">Managing Director</div>
    </div>
  </div>
</div>
</body>
</html>
```